Business Card Re-Design/Update

We'd like to update out business cards. I've included our current "Style guide" which has the colour scheme of the organisation in it. I've also included the branding files with logos etc in them.

I've also included a copy of one of our existing cards so that you can see how ugly/dated they look. I'd like a fresh modern corporate look.

Target Market(s)

These are for our clients, potential clients, industry contacts - like all business cards

Contact Information for Business Card

Name
Position
Company Address - Level 1, 47 Fernby Street, Carlow Qld 4072
Direct Phone
mobile
Email
Website -www.korvalit.com.au
Logo

Colors

Designer to choose colors to be used in the design.

Requirements
Must have
• Main Logo
• Cards will need to be editable to be able to personalize them for each new employee.
Nice to have
• The MapOut, ShipWell, KeepSteady would be okay to have if they can be sensibly and professionally added to the look without detracting from the main imagery.
• Maybe they could go on the back of the card? will leave this to your creative discretion as to whether/where they fit.
Should not have
• Should not have decorative or script fonts

```html
<!DOCTYPE html>
<html lang="en">
<head>
<meta charset="utf-8">
<title>Korvalit Business Card</title>
<link href="https://fonts.googleapis.com/css2?family=Work+Sans:wght@400;500;600&display=swap" rel="stylesheet">
<style>
  :root {
    --bg: #e4e4e6;
    --card-white: #ffffff;
    --card-dark: #2c2c2e;
    --brand-red: #d0121b;
    --text-dark: #2e2e30;
    --text-light: #d6d6d8;
  }
  * { margin: 0; padding: 0; box-sizing: border-box; }
  html, body { width: 1200px; height: 900px; overflow: hidden; }
  body {
    background: var(--bg);
    font-family: "Work Sans", Arial, sans-serif;
    display: flex;
    flex-direction: column;
    align-items: center;
    justify-content: center;
    gap: 56px;
  }
  .card {
    width: 600px;
    height: 343px;
    position: relative;
    box-shadow: 0 10px 28px rgba(0,0,0,0.18);
  }
  .card-front { background: var(--card-white); color: var(--text-dark); }
  .card-back { background: var(--card-dark); display: flex; align-items: center; justify-content: center; }

  .brand { display: flex; align-items: center; gap: 14px; }
  .brand-square { width: 34px; height: 34px; background: var(--brand-red); }
  .brand-name { font-weight: 500; font-size: 52px; letter-spacing: -1px; line-height: 1; }
  .card-front .brand { position: absolute; top: 56px; left: 50%; transform: translateX(-50%); }
  .card-front .brand-name { color: var(--text-dark); }
  .card-back .brand-name { color: var(--text-light); font-size: 62px; }
  .card-back .brand-square { width: 40px; height: 40px; }

  .divider { position: absolute; top: 150px; left: 40px; right: 40px; height: 2px; background: var(--brand-red); }

  .contact-list { position: absolute; left: 40px; top: 176px; list-style: none; font-size: 14px; line-height: 22px; }
  .contact-list li { display: flex; align-items: center; gap: 9px; }
  .contact-list svg { width: 12px; height: 12px; flex: none; }
  .web-accent { color: var(--brand-red); }

  .person { position: absolute; right: 40px; top: 176px; text-align: right; }
  .person-name { color: var(--brand-red); font-size: 26px; font-weight: 500; letter-spacing: 0.5px; line-height: 1.1; }
  .person-role { font-size: 14px; margin-top: 4px; }
  .person-address { font-size: 14px; line-height: 21px; margin-top: 26px; }
</style>
</head>
<body>
  <section class="card card-front">
    <div class="brand">
      <span class="brand-square"></span>
      <span class="brand-name">korvalit</span>
    </div>
    <div class="divider"></div>

    <ul class="contact-list">
      <li>
        <svg viewBox="0 0 12 12" aria-hidden="true"><rect x="3" y="0.5" width="6" height="11" rx="1.2" fill="none" stroke="#d0121b" stroke-width="1.3"/><circle cx="6" cy="9.3" r="0.8" fill="#d0121b"/></svg>
        +61 (0)400 555 014
      </li>
      <li>
        <svg viewBox="0 0 12 12" aria-hidden="true"><path d="M1 5 Q6 1 11 5 L9.5 6.5 L8 5.2 L4 5.2 L2.5 6.5 Z" fill="#d0121b"/><rect x="2.5" y="7" width="7" height="4" rx="0.8" fill="#d0121b"/></svg>
        +61 (0)7 5550 1216
      </li>
      <li>
        <svg viewBox="0 0 12 12" aria-hidden="true"><path d="M3 1 L5 3.5 L4 5 Q5 7.5 7 8 L8.5 7 L11 9 L9.5 11 Q3 10.5 1 3 Z" fill="#d0121b"/></svg>
        +61 (0)7 5550 1233
      </li>
      <li>
        <svg viewBox="0 0 12 12" aria-hidden="true"><rect x="1" y="4" width="10" height="6" rx="1" fill="#d0121b"/><rect x="3" y="1" width="6" height="3.5" fill="none" stroke="#d0121b" stroke-width="1.2"/></svg>
        +61 (0)7 5550 1203
      </li>
      <li>
        <svg viewBox="0 0 12 12" aria-hidden="true"><rect x="0.8" y="2.5" width="10.4" height="7" rx="1" fill="none" stroke="#d0121b" stroke-width="1.2"/><path d="M1 3 L6 7 L11 3" fill="none" stroke="#d0121b" stroke-width="1.2"/></svg>
        dwhitmore@korvalit.com.au
      </li>
      <li>
        <svg viewBox="0 0 12 12" aria-hidden="true"><circle cx="6" cy="6" r="5" fill="none" stroke="#d0121b" stroke-width="1.2"/><ellipse cx="6" cy="6" rx="2.2" ry="5" fill="none" stroke="#d0121b" stroke-width="1"/><path d="M1 6 H11" stroke="#d0121b" stroke-width="1"/></svg>
        <span>www.<span class="web-accent">korvalit</span>.com.au</span>
      </li>
    </ul>

    <div class="person">
      <p class="person-name">DANA WHITMORE</p>
      <p class="person-role">Business Development Manager</p>
      <p class="person-address">Level 1, 47 Fernby Street,<br>Carlow Qld 4072</p>
    </div>
  </section>

  <section class="card card-back">
    <div class="brand">
      <span class="brand-square"></span>
      <span class="brand-name">korvalit</span>
    </div>
  </section>
</body>
</html>
```